Redesign of business card for Cedar Ridge Mechanical

We are looking for a new design for our business cards for Cedar Ridge Mechanical. We are a plumbing & HVAC construction company, operating on the West Coast of Canada and USA. Logo attached.
Industry/Entity Type
Construction - Plumbing & HVAC
Contact Information for Business Card
Name, address, phone numbers, email, website address
Look and feel
Each slider illustrates characteristics of the customer's brand and the style your logo design should communicate.

```html
<!DOCTYPE html>
<html lang="en">
<head>
<meta charset="utf-8">
<title>Cedar Ridge Mechanical – Business Card</title>
<link rel="stylesheet" href="https://fonts.googleapis.com/css2?family=Poppins:wght@300;400;600;700&display=swap">
<style>
  :root {
    --stage: #232325;
    --card-ink: #1f1f21;
    --card-light: #ffffff;
    --text-light: #ffffff;
    --text-soft: #e6e6e6;
    --rule: #bdbdbd;
  }
  * { box-sizing: border-box; margin: 0; padding: 0; }
  html, body { width: 1200px; height: 711px; overflow: hidden; }
  body {
    background: var(--stage);
    font-family: "Poppins", sans-serif;
    color: var(--text-light);
    position: relative;
  }
  .card {
    position: absolute;
    top: 200px;
    width: 540px;
    height: 310px;
    border-radius: 24px;
    background: var(--card-light);
    overflow: hidden;
  }
  .card--front { left: 30px; }
  .card--back { left: 630px; }
  .card__oval {
    position: absolute;
    left: 9%;
    top: -38%;
    width: 82%;
    height: 176%;
    border-radius: 50%;
    background: var(--card-ink);
  }
  .brand {
    position: absolute;
    display: flex;
    align-items: center;
    gap: 12px;
  }
  .brand__mark {
    width: 30px;
    height: 30px;
    border: 4px solid var(--text-light);
    flex: none;
  }
  .brand__name {
    font-weight: 600;
    text-transform: uppercase;
    letter-spacing: 1px;
    line-height: 1.1;
    color: var(--text-light);
  }
  .card--front .brand { left: 0; right: 0; top: 130px; justify-content: center; }
  .card--front .brand__name { font-size: 24px; }
  .card--back .brand { left: 70px; top: 130px; }
  .card--back .brand__name { font-size: 15px; width: 150px; }
  .card--back .brand__mark { width: 22px; height: 22px; border-width: 3px; }
  .divider {
    position: absolute;
    left: 262px;
    top: 70px;
    width: 1px;
    height: 140px;
    background: var(--rule);
  }
  .contact {
    position: absolute;
    left: 290px;
    top: 62px;
  }
  .contact__name { font-size: 22px; font-weight: 300; letter-spacing: .3px; }
  .contact__name strong { font-weight: 700; }
  .contact__role { font-size: 11px; font-weight: 400; color: var(--text-soft); margin-top: -2px; }
  .contact__list { list-style: none; margin-top: 20px; }
  .contact__list li {
    display: flex; align-items: center; gap: 8px;
    font-size: 11px; font-weight: 300; color: var(--text-soft);
    line-height: 20px;
  }
  .contact__list svg { width: 11px; height: 11px; flex: none; }
  .address {
    position: absolute;
    left: 0; right: 0; bottom: 48px;
    text-align: center;
    font-size: 12px; font-weight: 300; color: var(--text-soft);
  }
</style>
</head>
<body>
  <section class="card card--front">
    <div class="card__oval"></div>
    <div class="brand">
      <span class="brand__mark"></span>
      <span class="brand__name">Cedar Ridge Mechanical</span>
    </div>
  </section>

  <section class="card card--back">
    <div class="card__oval"></div>
    <div class="brand">
      <span class="brand__mark"></span>
      <span class="brand__name">Cedar Ridge Mechanical</span>
    </div>
    <div class="divider"></div>
    <div class="contact">
      <p class="contact__name"><strong>Marta</strong> Kovarik</p>
      <p class="contact__role">Founder &amp; CEO</p>
      <ul class="contact__list">
        <li>
          <svg viewBox="0 0 24 24" fill="currentColor" aria-hidden="true"><path d="M6.6 10.8a15 15 0 0 0 6.6 6.6l2.2-2.2a1 1 0 0 1 1-.25 11.4 11.4 0 0 0 3.6.57 1 1 0 0 1 1 1V20a1 1 0 0 1-1 1A17 17 0 0 1 3 4a1 1 0 0 1 1-1h3.5a1 1 0 0 1 1 1c0 1.25.2 2.46.57 3.6a1 1 0 0 1-.25 1z"/></svg>
          (555) 214-0387
        </li>
        <li>
          <svg viewBox="0 0 24 24" fill="none" stroke="currentColor" stroke-width="2" aria-hidden="true"><circle cx="12" cy="12" r="9"/><path d="M3 12h18M12 3c3 3.5 3 14.5 0 18M12 3c-3 3.5-3 14.5 0 18"/></svg>
          info@cedarridgemech.com
        </li>
        <li>
          <svg viewBox="0 0 24 24" fill="none" stroke="currentColor" stroke-width="2" aria-hidden="true"><rect x="3" y="5" width="18" height="14" rx="1"/><path d="M3 6l9 7 9-7"/></svg>
          www.cedarridgemech.com
        </li>
      </ul>
    </div>
    <p class="address">1840 Alder Way Suite 310 Portland, OR 97205</p>
  </section>
</body>
</html>
```